Velkora Land Surveying Website Design

We are working with Velkora. They are a national land surveying company and in need of a new website design.

Some sites to use for inspiration:

https://brannickeng.com
https://www.dvwinc.com
https://kelvarin.com
https://gto.us
https://ravendobuilt.com
https://www.marbeckquillondale.com

Thank you for taking the time to consider designing a website for us. We are web developers based in Stockton and Los Angeles, CA, USA. Most of our projects go through the same process. Understanding this process may help you win a project with us. We custom-code all of our websites in-house. We don’t have any requirements as to what tools you use for your design, but we prefer Figma files. For any design that we label as four-stars, we send it to the client for review. The client picks the final design they want us to use. Once we complete this process, we will continue to show additional clients all the four-star sites and purchase them later. Your designs will have multiple chances to sell. For better chances of success, we ask that you follow these guidelines.

IMAGES:
If you use any images or icons in the design, we ask that you have a link to the asset so we can purchase the image/icon. Most of the designs we submit do not have the customer’s images on them unless they have some great images. Be creative; show us the feeling you are trying to portray with your image choices. Use any royalty-free site you choose. We subscribe to Pellix and mainly use their images, but we can purchase images outside of Pellix.

PLEASE NOTE: we will not submit designs to clients with watermarks on the images.

FONTS:
We ask that you identify the fonts used in the design. This can be done in a message if you want. We typically use Google Fonts and Pellix Fonts.

CONTENT:
We're always open to different content and ideas. We often submit designs with stock images so the client can see our vision. We typically take pictures after the website launch to use their images with our vision. Lorem Ipsum is fine for paragraphs, but we ask that you write the headers in correct English. We want to be able to show the vision and identify the sections of the website.

INSPIRATION:
We typically add a couple of links in the brief of websites we like to help you get started in your design.

REVISIONS:
We do not often ask for revisions of the designs unless we see something in the design that may not appeal to the client. If there are slight changes that we want to make, we do that in the development process.

FEEDBACK:
We rarely give feedback on designs during the design process. We are working on many website projects and do not have the time to provide feedback. We usually respond if your request is well thought out and asks specific questions, but a note asking “feedback, please” usually goes unanswered.

```html
<!DOCTYPE html>
<html lang="en">
<head>
<meta charset="utf-8">
<title>Velkora Land Surveying</title>
<link href="https://fonts.googleapis.com/css2?family=Teko:wght@400;500;600&family=Poppins:wght@300;400;500&display=swap" rel="stylesheet">
<style>
:root{
  --orange:#E98B25;
  --orange-dark:#D97A17;
  --ink:#3A3834;
  --brown:#4A4540;
  --brown-line:#5F5953;
  --muted:#6B6762;
  --tile:#EFEEEC;
  --white:#ffffff;
}
*{box-sizing:border-box;margin:0;padding:0}
html,body{width:1200px;height:4307px;overflow:hidden;background:var(--white)}
body{position:relative;font-family:"Poppins",sans-serif;color:var(--ink)}
.abs{position:absolute}
.display{font-family:"Teko",sans-serif;font-weight:500;text-transform:uppercase;line-height:.9;letter-spacing:.3px}
.brand{font-family:"Teko",sans-serif;font-weight:600;font-size:44px;line-height:1;letter-spacing:1px;color:var(--orange);white-space:nowrap}
.header-brand{left:104px;top:16px}
.footer-brand{left:150px;top:3910px}

/* header */
.site-header{top:0;left:0;width:1200px;height:72px;background:var(--white)}
.main-nav{right:104px;top:27px;display:flex;gap:26px;align-items:center}
.main-nav span{font-family:"Teko",sans-serif;font-size:17px;color:var(--ink);letter-spacing:.3px;text-transform:uppercase;line-height:1}
.main-nav .caret{font-size:11px;margin-left:3px}

/* hero */
.hero{top:72px;left:0;width:1200px;height:647px;background:linear-gradient(100deg,#4b4640 0%,#6b655c 35%,#9a9383 55%,#c98a3d 72%,#6f6a62 100%)}
.hero-shade{top:72px;left:0;width:700px;height:647px;background:linear-gradient(90deg,rgba(30,28,25,.55),rgba(30,28,25,0))}
.hero-title{left:104px;top:236px;font-size:68px;color:var(--white);line-height:.88}
.hero-sub{left:104px;top:442px;font-family:"Teko",sans-serif;font-size:17px;line-height:1.3;color:var(--white);text-transform:uppercase;letter-spacing:.2px}
.btn{display:flex;align-items:center;justify-content:center;font-family:"Teko",sans-serif;font-size:15px;text-transform:uppercase;letter-spacing:.3px}
.btn-quote{left:104px;top:503px;width:152px;height:42px;background:var(--orange);color:var(--white)}
.btn-services{left:264px;top:503px;width:152px;height:42px;background:var(--white);color:var(--ink)}
.hero-arrows{left:104px;top:652px}

/* who we are */
.section-title{font-size:42px;color:var(--ink)}
.who-title{left:112px;top:790px}
.stats-panel{left:112px;top:844px;width:366px;height:465px;background:var(--orange)}
.stat{left:174px;color:var(--white)}
.stat-num{font-family:"Teko",sans-serif;font-weight:500;font-size:72px;line-height:.8}
.stat-label{font-family:"Teko",sans-serif;font-size:12px;text-transform:uppercase;margin-top:4px}
.stat-rule{left:174px;width:119px;height:1px;background:rgba(255,255,255,.6)}
.field-photo{left:343px;top:903px;width:299px;height:348px;background:linear-gradient(150deg,#9ccf4d 0%,#6aa136 40%,#3d6e2a 70%,#7e6a4a 100%)}
.eyebrow{font-family:"Teko",sans-serif;font-size:13px;color:var(--orange);text-transform:uppercase;letter-spacing:.3px}
.about-eyebrow{left:700px;top:968px}
.about-title{left:700px;top:990px;font-size:44px;color:var(--ink)}
.body-copy{font-size:11.5px;line-height:1.62;color:var(--muted)}
.about-copy{left:700px;top:1090px;width:360px}

/* services */
.services-title{left:0;width:1200px;text-align:center;top:1396px}
.services-sub{left:0;width:1200px;text-align:center;top:1441px;font-size:12px;color:var(--muted)}
.service-card{top:1486px;width:328px;height:373px}
.service-card .label{position:absolute;left:44px;bottom:26px;font-family:"Teko",sans-serif;font-weight:500;font-size:23px;line-height:.95;color:var(--white);text-transform:uppercase;z-index:1}
.service-card::after{content:"";position:absolute;inset:0;background:linear-gradient(180deg,rgba(0,0,0,0) 55%,rgba(0,0,0,.55))}
.card-1{left:-72px;background:linear-gradient(160deg,#9aa39a,#7f8a6a 50%,#c77a2a 80%)}
.card-2{left:267px;background:linear-gradient(180deg,#b9c6c9,#a8b49a 55%,#5d6b3b)}
.card-3{left:607px;background:linear-gradient(170deg,#a9aaa9,#6a6c6c 55%,#3c3d3d)}
.card-4{left:945px;background:linear-gradient(180deg,#c9d3da,#6e8aa2 45%,#3f6a3c 80%)}
.slider-btn{top:1894px;width:28px;height:28px;display:flex;align-items:center;justify-content:center;color:var(--white);font-size:12px}
.slider-prev{left:570px;background:var(--orange)}
.slider-next{left:601px;background:var(--brown)}

/* difference */
.diff-panel{left:0;top:2008px;width:607px;height:493px;background:var(--brown)}
.diff-photo{left:607px;top:2008px;width:593px;height:493px;background:linear-gradient(160deg,#cdd8de 0%,#aebac0 40%,#7d6f5c 70%,#c47b2a 100%)}
.diff-title{left:104px;top:2093px;font-size:42px;color:var(--white)}
.diff-item{left:104px;display:flex;gap:18px;align-items:center}
.icon-box{width:58px;height:58px;background:var(--orange);display:flex;align-items:center;justify-content:center;flex:none}
.diff-item h3{font-family:"Teko",sans-serif;font-weight:500;font-size:17px;color:var(--white);text-transform:uppercase;line-height:1}
.diff-item p{font-size:11px;color:#e6e2dd;margin-top:2px}
.diff-rule{left:180px;width:313px;height:1px;background:var(--brown-line)}

/* industries */
.trusted-title{left:0;width:1200px;text-align:center;top:2598px}
.trusted-sub{left:0;width:1200px;text-align:center;top:2645px;font-size:12px;color:var(--muted)}
.industries{left:147px;top:2693px;display:flex;gap:15px}
.industry{width:169px;height:181px;background:var(--tile);display:flex;flex-direction:column;align-items:center;padding-top:28px}
.industry span{font-family:"Teko",sans-serif;font-weight:500;font-size:16px;line-height:1;text-transform:uppercase;text-align:center;color:var(--ink);margin-top:18px}

/* projects */
.projects-panel{left:538px;top:2978px;width:557px;height:496px;background:var(--orange)}
.projects-photo{left:104px;top:3035px;width:498px;height:384px;background:linear-gradient(135deg,#5a6e3c 0%,#8a7f62 35%,#5f8aa8 55%,#3d5f78 70%,#6f7a4a 100%)}
.projects-eyebrow{left:669px;top:3060px;color:var(--white)}
.projects-title{left:669px;top:3082px;font-size:48px;color:var(--white)}
.projects-card{left:670px;top:3187px;width:372px;height:135px;background:var(--white);padding:22px 26px}
.btn-browse{left:670px;top:3351px;width:151px;height:40px;background:var(--brown);color:var(--white)}
.btn-phone{left:826px;top:3351px;width:43px;height:40px;background:var(--brown)}
.questions{left:881px;top:3362px;font-family:"Teko",sans-serif;font-weight:500;font-size:18px;color:var(--white);text-transform:uppercase;line-height:1}

/* closing */
.closing{left:0;width:1200px;text-align:center;top:3568px;font-size:58px;line-height:1.03;color:var(--ink)}

/* footer */
.site-footer{left:0;top:3849px;width:1200px;height:458px;background:var(--brown)}
.contact{display:flex;gap:16px;align-items:center}
.contact-icon{width:51px;height:50px;border:1px solid var(--brown-line);display:flex;align-items:center;justify-content:center;flex:none}
.contact small{display:block;font-size:11px;color:#cfc9c2}
.contact strong{display:block;font-weight:500;font-size:22px;color:var(--white);line-height:1.1;white-space:nowrap}
.footer-rule{left:150px;top:4018px;width:900px;height:1px;background:var(--brown-line)}
.socials{left:152px;top:4078px;display:flex;gap:10px}
.socials span{width:40px;height:40px;border:1px solid var(--brown-line);display:flex;align-items:center;justify-content:center}
.socials i{width:10px;height:10px;background:var(--white);display:block}
.copyright{left:152px;top:4153px;font-size:11px;line-height:1.6;color:#cfc9c2}
.footer-col h4{font-family:"Teko",sans-serif;font-weight:500;font-size:17px;color:var(--white);text-transform:uppercase;line-height:1;margin-bottom:14px}
.footer-col li{list-style:none;font-size:10.5px;color:#cfc9c2;line-height:26px}
.newsletter-field{left:794px;top:4116px;width:252px;height:27px;border-bottom:1px solid var(--brown-line);font-size:13px;color:var(--white);font-weight:500}
.no-spam{left:794px;top:4160px;font-size:11px;color:#8d8680}
</style>
</head>
<body>

<header class="abs site-header">
  <nav class="abs main-nav">
    <span>Legacy<span class="caret">&#8964;</span></span>
    <span>Expertise<span class="caret">&#8964;</span></span>
    <span>Projects<span class="caret">&#8964;</span></span>
    <span>Careers<span class="caret">&#8964;</span></span>
    <span>Insights</span>
    <span>Connect</span>
    <svg width="16" height="16" viewBox="0 0 16 16" fill="none" stroke="#3A3834" stroke-width="1.5"><circle cx="7" cy="7" r="5"/><path d="M11 11l4 4"/></svg>
  </nav>
</header>
<div class="abs brand header-brand">VELKORA</div>

<section>
  <div class="abs hero" role="img" aria-label="Surveyor in hard hat and high-visibility vest operating a total station beside a road"></div>
  <div class="abs hero-shade"></div>
  <h1 class="abs display hero-title">Balancing the<br>natural and built<br>environment</h1>
  <p class="abs hero-sub">Delivering trusted land surveying solutions with accuracy,<br>innovation, and care for over 15 years.</p>
  <a class="abs btn btn-quote">Request a Quote</a>
  <a class="abs btn btn-services">View Our Services</a>
  <svg class="abs hero-arrows" width="76" height="20" viewBox="0 0 76 20" fill="none" stroke="#fff" stroke-width="1.6"><path d="M32 10H2M9 3L2 10l7 7"/><path d="M44 10h30M67 3l7 7-7 7"/></svg>
</section>

<section>
  <h2 class="abs display section-title who-title">Who We Are</h2>
  <div class="abs stats-panel"></div>
  <div class="abs stat" style="top:900px"><div class="stat-num">140+</div><div class="stat-label">Success ful projects</div></div>
  <div class="abs stat-rule" style="top:1005px"></div>
  <div class="abs stat" style="top:1040px"><div class="stat-num">35+</div><div class="stat-label">Team members</div></div>
  <div class="abs stat-rule" style="top:1142px"></div>
  <div class="abs stat" style="top:1182px"><div class="stat-num">80+</div><div class="stat-label">Happy clients</div></div>
  <div class="abs field-photo" role="img" aria-label="Aerial view of green farmland fields and tree lines"></div>
  <div class="abs eyebrow about-eyebrow">About Us</div>
  <h2 class="abs display about-title">Over 25 years of trusted<br>general contracting</h2>
  <p class="abs body-copy about-copy">Velkora is a leading national land surveying company providing comprehensive surveying and mapping solutions. Our team of experts combines decades of experience with the latest technology to deliver precise, reliable results for clients across industries.</p>
</section>

<section>
  <h2 class="abs display section-title services-title">Our Services</h2>
  <p class="abs services-sub">From boundary surveys to advanced geospatial mapping, we cover it all.</p>
  <div class="abs service-card card-1" role="img" aria-label="Surveyor with GNSS receiver on tripod in a field"><div class="label">Boundary &amp; Topographic<br>Surveys</div></div>
  <div class="abs service-card card-2" role="img" aria-label="Surveyor with instrument in open grassland"><div class="label">ALTA/NSPS Land Title<br>Surveys</div></div>
  <div class="abs service-card card-3" role="img" aria-label="3D laser scanner inside a tunnel"><div class="label">3D Laser Scanning &amp;<br>Mapping</div></div>
  <div class="abs service-card card-4" role="img" aria-label="Survey drone flying over a lake and forest"><div class="label">Drone and Aerial<br>Surveying</div></div>
  <div class="abs slider-btn slider-prev">&#8249;</div>
  <div class="abs slider-btn slider-next">&#8250;</div>
</section>

<section>
  <div class="abs diff-panel"></div>
  <div class="abs diff-photo" role="img" aria-label="Surveyor looking through a total station on a construction site"></div>
  <h2 class="abs display diff-title">The Velkora Difference</h2>
  <div class="abs diff-item" style="top:2155px">
    <div class="icon-box"><svg width="32" height="32" viewBox="0 0 32 32" fill="none" stroke="#fff" stroke-width="1.4"><circle cx="16" cy="16" r="7"/><circle cx="16" cy="16" r="2"/><path d="M3 9V3h6M23 3h6v6M29 23v6h-6M9 29H3v-6"/></svg></div>
    <div><h3>Accuracy First</h3><p>Every project backed by rigorous quality control.</p></div>
  </div>
  <div class="abs diff-rule" style="top:2238px"></div>
  <div class="abs diff-item" style="top:2250px">
    <div class="icon-box"><svg width="32" height="32" viewBox="0 0 32 32" fill="none" stroke="#fff" stroke-width="1.4"><circle cx="16" cy="16" r="12"/><ellipse cx="16" cy="16" rx="5" ry="12"/><path d="M4 16h24M6 10h20M6 22h20"/></svg></div>
    <div><h3>Nationwide Reach</h3><p>Serving clients across the United States.</p></div>
  </div>
  <div class="abs diff-rule" style="top:2334px"></div>
  <div class="abs diff-item" style="top:2345px">
    <div class="icon-box"><svg width="32" height="32" viewBox="0 0 32 32" fill="none" stroke="#fff" stroke-width="1.4"><path d="M11 19a8 8 0 1 1 10 0v4H11z"/><path d="M12 26h8M13 29h6M16 2v2M4 14H2M30 14h-2M7 6L5 4M25 6l2-2"/></svg></div>
    <div><h3>Innovative Technology</h3><p>Using drones, 3D scanners, and GIS systems.</p></div>
  </div>
</section>

<section>
  <h2 class="abs display section-title trusted-title">Trusted by Industries Nationwide</h2>
  <p class="abs trusted-sub">We partner with clients in multiple sectors, delivering dependable survey data that drives successful projects.</p>
  <div class="abs industries">
    <div class="industry">
      <svg width="76" height="76" viewBox="0 0 76 76" fill="none" stroke="#3A3834" stroke-width="1.6"><path d="M4 72h68M10 72V34h16v38M26 72V14h20v58M46 72V40h20v32"/><path d="M31 22h4M37 22h4M31 30h4M37 30h4M31 38h4M37 38h4M51 48h4M57 48h4M51 56h4M57 56h4M14 42h4M14 50h4"/></svg>
      <span>Commercial<br>Real Estate</span>
    </div>
    <div class="industry">
      <svg width="76" height="76" viewBox="0 0 76 76" fill="none" stroke="#3A3834" stroke-width="1.6"><rect x="20" y="6" width="36" height="34"/><path d="M26 14h6M36 14h6M46 14h4M26 22h6M36 22h6M46 22h4M26 30h6M36 30h6M46 30h4"/><circle cx="38" cy="56" r="12"/><circle cx="38" cy="56" r="4"/><path d="M38 40v4M38 68v4M22 56h4M50 56h4"/></svg>
      <span>Construction &amp;<br>Infrastructure</span>
    </div>
    <div class="industry">
      <svg width="76" height="76" viewBox="0 0 76 76" fill="none" stroke="#3A3834" stroke-width="1.6"><path d="M36 4L22 72M36 4l14 68M18 20h36M14 34h44M26 52h20M24 62h24"/><circle cx="58" cy="60" r="10"/><path d="M60 52l-5 9h6l-4 8"/></svg>
      <span>Energy &amp;<br>Utilities</span>
    </div>
    <div class="industry">
      <svg width="76" height="76" viewBox="0 0 76 76" fill="none" stroke="#3A3834" stroke-width="1.6"><path d="M6 72h64M10 66h56M12 34h52M20 34a18 14 0 0 1 36 0M38 8v12M38 8h8v5h-8"/><path d="M16 40v22M26 40v22M36 40v22M46 40v22M56 40v22"/></svg>
      <span>Government &amp;<br>Municipalities</span>
    </div>
    <div class="industry">
      <svg width="76" height="76" viewBox="0 0 76 76" fill="none" stroke="#3A3834" stroke-width="1.6"><path d="M28 8h40v22H28zM34 14h4M42 14h4M50 14h4M58 14h4M18 4v14M12 10h12"/><path d="M6 36h56l-6 10H10zM6 54h40v10H6z"/><circle cx="14" cy="66" r="3"/><circle cx="38" cy="66" r="3"/></svg>
      <span>Transportation</span>
    </div>
  </div>
</section>

<section>
  <div class="abs projects-panel"></div>
  <div class="abs projects-photo" role="img" aria-label="Aerial view of a dredging barge on a river channel between farmland"></div>
  <div class="abs eyebrow projects-eyebrow">Our Projects</div>
  <h2 class="abs display projects-title">Projects that reflect<br>our purpose</h2>
  <div class="abs projects-card"><p class="body-copy">Velkora is a leading national land surveying company providing comprehensive surveying and mapping solutions. Our team of experts combines decades of experience with the latest technology to deliver precise, reliable results for clients across industries.</p></div>
  <a class="abs btn btn-browse">Browse Projects</a>
  <div class="abs btn btn-phone"><svg width="16" height="16" viewBox="0 0 24 24" fill="#fff"><path d="M6.6 10.8a15.1 15.1 0 0 0 6.6 6.6l2.2-2.2a1 1 0 0 1 1-.25 11.4 11.4 0 0 0 3.6.57 1 1 0 0 1 1 1V20a1 1 0 0 1-1 1A17 17 0 0 1 3 4a1 1 0 0 1 1-1h3.5a1 1 0 0 1 1 1c0 1.25.2 2.45.57 3.57a1 1 0 0 1-.25 1z"/></svg></div>
  <div class="abs questions">Have Questions?</div>
</section>

<section>
  <h2 class="abs display closing">From preconstruction to punch<br>list, we’re with you every step<br>of the way.</h2>
</section>

<footer>
  <div class="abs site-footer"></div>
  <div class="abs brand footer-brand">VELKORA</div>
  <div class="abs contact" style="left:481px;top:3906px">
    <div class="contact-icon"><svg width="18" height="18" viewBox="0 0 24 24" fill="#E98B25"><path d="M6.6 10.8a15.1 15.1 0 0 0 6.6 6.6l2.2-2.2a1 1 0 0 1 1-.25 11.4 11.4 0 0 0 3.6.57 1 1 0 0 1 1 1V20a1 1 0 0 1-1 1A17 17 0 0 1 3 4a1 1 0 0 1 1-1h3.5a1 1 0 0 1 1 1c0 1.25.2 2.45.57 3.57a1 1 0 0 1-.25 1z"/></svg></div>
    <div><small>Call us Now</small><strong>+1 555 014 2290</strong></div>
  </div>
  <div class="abs contact" style="left:749px;top:3906px">
    <div class="contact-icon"><svg width="18" height="14" viewBox="0 0 18 14" fill="#E98B25"><path d="M0 0h18v2L9 8 0 2z"/><path d="M0 4l9 6 9-6v10H0z"/></svg></div>
    <div><small>Write to us</small><strong style="font-size:20px">hello@velkora-survey.com</strong></div>
  </div>
  <div class="abs footer-rule"></div>
  <div class="abs socials" aria-label="Social media links"><span><i></i></span><span><i></i></span><span><i></i></span></div>
  <p class="abs copyright">© Copyright Velkora 2025.<br>All Rights Reserved</p>
  <div class="abs footer-col" style="left:416px;top:4080px">
    <h4>Quick Links</h4>
    <ul><li>Legacy</li><li>Expertise</li><li>Projects</li><li>Careers</li><li>Insights</li></ul>
  </div>
  <div class="abs footer-col" style="left:592px;top:4080px">
    <h4>Information</h4>
    <ul><li>Terms &amp; Condition</li><li>Privacy Policy</li><li>Disclaimer</li><li>FAQ</li><li>Client Reviews</li></ul>
  </div>
  <div class="abs footer-col" style="left:794px;top:4080px"><h4>Subscribe to our newsletter</h4></div>
  <div class="abs newsletter-field">hello@velkora-survey.com
    <svg style="position:absolute;right:4px;top:3px" width="12" height="12" viewBox="0 0 12 12" fill="#E98B25"><path d="M0 5L12 0 7 12 5.5 6.5z"/></svg>
  </div>
  <p class="abs no-spam">*We don’t spam</p>
</footer>

</body>
</html>
```